Creation of a construction/bricklaying business website

Following the template format of "Halloway 7", the following content would need to be included:
1. Landing page with 3 tiles that go to their own pages.
- Landing page to include background photo and description of services offered.
2. 3 tiles to include:
a) "Contact Us For A Free Quote or Friendly Discussion" Form (middle tile)
b) Case Studies and Testimonials
c) Certifications and Professional Membership
- Design logo to be used from previous SketchNestle project. Example of logo attached below, please access full JPG files from our account.

Target Market(s)

Prospective clients seeking construction work (bricklaying speciality)

Industry/Entity Type

Residential Construction

Coding

Coded - Design and coding required

Number of Pages Required

4 page

Font styles to use
Sans Serif

Colors

Designer to choose colors to be used in the design.

Requirements
Must have
• Following the template format of "Halloway 7", the following content would need to be included:
• 1. Landing parent page with 3 tiles that go to the 3 child pages.
• - Landing page to include background photo and description of services offered.
• 2. 3 tiles to include:
• a) "Contact Us For A Free Quote or Friendly Discussion" Form (middle tile)
• b) Case Studies and Testimonials (first tile / left side)
• c) Certifications and Professional Memberships (third tile / right side) (This should include logos of the relevant organisations being displayed. Specifically GQT and the Pillar Seal GQT).
• - Design logo to be used from previous SketchNestle project. Example of logo attached below, please access full JPG files from our account.
Nice to have
• Sleek and modern feel.
• Approachable in terms of how people can contact the company for a quote.
• Traditional pictures to give credibility and comfort around choosing this company.
Should not have
• Cheesy pictures
• Over-complicated
• Simple to use
• Easy URL domain name

```html
<!DOCTYPE html>
<html lang="en">
<head>
<meta charset="utf-8">
<title>R.T.Marlow Construction Ltd</title>
<link href="https://fonts.googleapis.com/css2?family=Jost:wght@400;500;600&display=swap" rel="stylesheet">
<style>
:root{
  --blue:#0d55a6;
  --ink:#2b2b2b;
  --text:#1a1a1a;
  --tile:#e6eaea;
  --white:#ffffff;
  --hero-a:#6b3a2c;
  --hero-b:#3e2a26;
  --foot-a:#3b2a24;
  --foot-b:#22201f;
}
*{box-sizing:border-box;margin:0;padding:0}
html,body{width:920px;height:1200px;overflow:hidden;background:var(--white);font-family:"Jost",sans-serif;color:var(--text)}
.page{position:relative;width:920px;height:1200px}

.hero{position:absolute;left:0;top:0;width:920px;height:315px;
  background:linear-gradient(160deg,#7d4a38 0%,var(--hero-a) 40%,#55433d 70%,var(--hero-b) 100%)}
.contact-chip{position:absolute;display:flex;align-items:center;gap:8px;color:var(--white);font-size:11px;line-height:16px}
.chip-icon{width:29px;height:29px;border-radius:50%;background:var(--blue);display:flex;align-items:center;justify-content:center;flex:none}
.hero .phone{left:124px;top:13px}
.hero .mail{left:626px;top:12px}
.brand{position:absolute;left:0;width:920px;text-align:center;color:var(--white);font-weight:600;letter-spacing:1px}
.hero .brand{top:128px;font-size:44px;line-height:46px}
.hero .brand small{display:block;font-size:17px;line-height:22px;letter-spacing:3px}

.nav{position:absolute;left:0;top:315px;width:920px;height:36px;background:var(--blue);display:flex;align-items:center;padding-left:131px;gap:19px;font-size:12.5px;font-weight:500}
.nav a{color:var(--white);text-decoration:none;letter-spacing:.3px}
.nav a.current{color:#0b1b33}

.about-title{position:absolute;top:380px;width:920px;text-align:center;color:var(--blue);font-size:21px;font-weight:500}
.about-lead{position:absolute;top:421px;left:160px;width:600px;text-align:center;font-size:14.5px;line-height:18px;color:var(--ink);font-weight:500;letter-spacing:.3px}

.service{position:absolute;top:482px;width:120px;text-align:center}
.service .ring{width:78px;height:78px;margin:0 auto;border:3px solid var(--blue);border-radius:50%;background:radial-gradient(circle at 50% 40%,#ffffff,#dcdcdc);display:flex;align-items:center;justify-content:center}
.service .shade{width:60px;height:4px;margin:3px auto 0;border-radius:50%;background:#e2e2e2}
.service p{margin-top:14px;font-size:15px;line-height:18px;color:var(--ink);font-weight:500}

.intro{position:absolute;top:645px;left:125px;width:670px;text-align:center;font-size:12px;line-height:18.5px}
.intro p+p{margin-top:12px}

.tile{position:absolute;top:753px;width:224px;height:209px;text-align:center;padding-top:22px}
.tile.grey{background:var(--tile)}
.tile .art{height:52px;display:flex;justify-content:center;align-items:flex-end;gap:4px}
.tile h3{margin:12px auto 0;width:150px;font-size:10.5px;line-height:14px;font-weight:600;color:var(--text)}
.tile p{margin:12px auto 0;width:212px;font-size:10px;line-height:16.5px}
.tile a{display:block;margin-top:10px;color:var(--blue);font-size:11px;font-weight:500;text-decoration:none}

.footer{position:absolute;left:0;top:1007px;width:920px;height:193px;background:linear-gradient(180deg,var(--foot-a),var(--foot-b))}
.footer .brand{top:37px;font-size:19px;line-height:20px;opacity:.9}
.footer .brand small{display:block;font-size:7.5px;line-height:10px;letter-spacing:1.5px}
.footer .contact-chip{top:85px}
.footer .addr{left:146px}
.footer .tel{left:393px}
.footer .em{left:597px}
.copyright{position:absolute;left:146px;top:162px;color:var(--white);font-size:10.5px}
.social{position:absolute;left:662px;top:155px;display:flex;gap:6px}
.social span{width:23px;height:23px;border-radius:50%;background:var(--white);border:2px solid var(--blue)}
</style>
</head>
<body>
<div class="page">

  <header class="hero" role="img" aria-label="Photo of a newly built brick garden wall in front of terraced houses">
    <div class="contact-chip phone">
      <span class="chip-icon"><svg width="14" height="14" viewBox="0 0 24 24"><path fill="#fff" d="M6.6 10.8a15 15 0 006.6 6.6l2.2-2.2a1 1 0 011-.25 11.4 11.4 0 003.6.6 1 1 0 011 1V20a1 1 0 01-1 1A17 17 0 013 4a1 1 0 011-1h3.5a1 1 0 011 1c0 1.25.2 2.45.6 3.6a1 1 0 01-.25 1z"/></svg></span>
      <span>Call Us On<br>123.456.7890</span>
    </div>
    <div class="contact-chip mail">
      <span class="chip-icon"><svg width="15" height="11" viewBox="0 0 16 11"><rect x=".5" y=".5" width="15" height="10" fill="none" stroke="#fff"/><path d="M.5.5l7.5 6 7.5-6M.5 10.5l5.5-5M15.5 10.5l-5.5-5" fill="none" stroke="#fff"/></svg></span>
      <span>Email Us On<br>info@rtmarlowbuild.com</span>
    </div>
    <div class="brand">R.T.Marlow<small>CONSTRUCTION LTD</small></div>
  </header>

  <nav class="nav">
    <a class="current" href="#">Home</a>
    <a href="#">Case Studies &amp; Testimonials</a>
    <a href="#">Contact Us For A Free Quote</a>
    <a href="#">Certifications &amp; Professional Memberships</a>
  </nav>

  <h1 class="about-title">About Us</h1>
  <p class="about-lead">R.T.Marlow Construction Ltd is a construction company that has expertise and experience in the following areas</p>

  <div class="service" style="left:103px">
    <div class="ring"><svg width="40" height="36" viewBox="0 0 40 36"><path d="M6 16L20 5l14 11" fill="none" stroke="#333" stroke-width="2"/><rect x="9" y="15" width="22" height="15" fill="none" stroke="#333" stroke-width="2"/><rect x="13" y="19" width="5" height="5" fill="#333"/><rect x="22" y="19" width="5" height="11" fill="#333"/><path d="M4 34h32" stroke="#333"/></svg></div>
    <div class="shade"></div><p>Extensions</p>
  </div>
  <div class="service" style="left:221px">
    <div class="ring"><svg width="40" height="36" viewBox="0 0 40 36"><path d="M4 18L20 4l16 14" fill="none" stroke="#333" stroke-width="3"/><rect x="9" y="17" width="22" height="16" fill="none" stroke="#333" stroke-width="3"/><rect x="14" y="21" width="5" height="5" fill="#333"/><rect x="22" y="22" width="5" height="11" fill="#333"/><rect x="27" y="5" width="4" height="8" fill="#333"/></svg></div>
    <div class="shade"></div><p>New build /<br>New houses</p>
  </div>
  <div class="service" style="left:346px">
    <div class="ring"><svg width="48" height="34" viewBox="0 0 48 34"><g fill="#333"><rect x="2" y="2" width="44" height="5"/><rect x="2" y="9" width="13" height="5"/><rect x="17" y="9" width="14" height="5"/><rect x="33" y="9" width="13" height="5"/><rect x="2" y="16" width="20" height="5"/><rect x="24" y="16" width="22" height="5"/><rect x="2" y="23" width="13" height="5"/><rect x="17" y="23" width="14" height="5"/><rect x="33" y="23" width="13" height="5"/><rect x="2" y="30" width="44" height="3"/></g></svg></div>
    <div class="shade"></div><p>Garden walls</p>
  </div>
  <div class="service" style="left:459px">
    <div class="ring"><svg width="46" height="36" viewBox="0 0 46 36"><g fill="none" stroke="#333" stroke-width="2"><rect x="3" y="4" width="28" height="26"/><path d="M3 11h28M3 18h28M3 24h28M14 4v7M22 11v7M12 18v6M22 24v6"/><path d="M30 14l12 16-4 3-12-16z" fill="#333"/></g></svg></div>
    <div class="shade"></div><p>Plastering</p>
  </div>
  <div class="service" style="left:578px">
    <div class="ring"><svg width="46" height="36" viewBox="0 0 46 36"><g fill="#333"><rect x="7" y="2" width="3" height="12"/><path d="M3 14h11l-5.5 10z"/><rect x="18" y="16" width="8" height="4"/><rect x="28" y="16" width="10" height="4"/><rect x="14" y="22" width="10" height="4"/><rect x="26" y="22" width="14" height="4"/><rect x="10" y="28" width="12" height="4"/><rect x="24" y="28" width="16" height="4"/></g></svg></div>
    <div class="shade"></div><p>Brickwork</p>
  </div>
  <div class="service" style="left:698px">
    <div class="ring"><svg width="46" height="38" viewBox="0 0 46 38"><g fill="#333"><rect x="6" y="2" width="12" height="3"/><rect x="10" y="4" width="3" height="16"/><path d="M5 20h13v10a6.5 6.5 0 01-13 0z"/><path d="M21 34l9-12 6 6 7 6z"/><circle cx="40" cy="26" r="2"/></g></svg></div>
    <div class="shade"></div><p>Groundworks</p>
  </div>

  <section class="intro">
    <p>We pride ourselves on attention to detail, pride in our completed project and client satisfaction. We believe in full transparency and this is reflected in the jobs we quote for you. We break down each step with both labour and materials cost so you can see exactly what you are paying for.</p>
    <p>Feel free to get in touch and we can talk through what you are looking to achieve.</p>
  </section>

  <article class="tile grey" style="left:124px">
    <div class="art"><svg width="74" height="50" viewBox="0 0 74 50"><rect x="30" y="2" width="38" height="44" rx="3" fill="#fff" stroke="#1c4f8c" stroke-width="2"/><path d="M36 10h26M36 16h26M36 22h14M36 40h18" stroke="#6b7c90" stroke-width="2"/><circle cx="56" cy="30" r="8" fill="#fff" stroke="#1c4f8c" stroke-width="2.5"/><path d="M61 36l8 8" stroke="#1c4f8c" stroke-width="3"/><ellipse cx="12" cy="32" rx="11" ry="9" fill="#1c4f8c"/><ellipse cx="27" cy="26" rx="8" ry="7" fill="#8a8f96"/></svg></div>
    <h3>Case Studies and Testimonials</h3>
    <p>Ut wisi enim ad minim veniam, quis nostrud exerci tation ullamcorper suscipit lobortis nisl ut aliquip ex ea commodo consequat.</p>
    <a href="#">Read More</a>
  </article>

  <article class="tile" style="left:348px">
    <div class="art"><svg width="46" height="50" viewBox="0 0 46 50"><path d="M6 2h26l10 10v36H6z" fill="#fff" stroke="#1c4f8c" stroke-width="2.5"/><path d="M32 2v10h10" fill="none" stroke="#1c4f8c" stroke-width="2.5"/><path d="M18 20h18M18 26h18M18 32h18" stroke="#1c4f8c" stroke-width="2"/><path d="M2 36l5 8 10-16" fill="none" stroke="#444" stroke-width="3"/></svg></div>
    <h3>Contact Us For A<br>Free Quote</h3>
    <p>Ut wisi enim ad minim veniam, quis nostrud exerci tation ullamcorper suscipit lobortis nisl ut aliquip ex ea commodo consequat.</p>
    <a href="#">Contact Us</a>
  </article>

  <article class="tile grey" style="left:572px">
    <div class="art"><svg width="66" height="50" viewBox="0 0 66 50" role="img" aria-label="Membership badges"><rect x="2" y="2" width="28" height="46" fill="#c8102e"/><rect x="36" y="2" width="28" height="46" fill="#c8102e"/></svg></div>
    <h3>Certifications and Professional Memberships</h3>
    <p>Ut wisi enim ad minim veniam, quis nostrud exerci tation ullamcorper suscipit lobortis nisl ut aliquip ex ea commodo consequat.</p>
    <a href="#">Know More</a>
  </article>

  <footer class="footer" role="img" aria-label="Dimmed photo of modern brick family homes">
    <div class="brand">R.T.Marlow<small>CONSTRUCTION LTD</small></div>
    <div class="contact-chip addr">
      <span class="chip-icon"><svg width="12" height="15" viewBox="0 0 12 16"><path fill="#fff" d="M6 0a6 6 0 016 6c0 4.5-6 10-6 10S0 10.5 0 6a6 6 0 016-6z"/><circle cx="6" cy="6" r="2.2" fill="#0d55a6"/></svg></span>
      <span>Street Name, City Name<br>State Zipcode</span>
    </div>
    <div class="contact-chip tel">
      <span class="chip-icon"><svg width="14" height="14" viewBox="0 0 24 24"><path fill="#fff" d="M6.6 10.8a15 15 0 006.6 6.6l2.2-2.2a1 1 0 011-.25 11.4 11.4 0 003.6.6 1 1 0 011 1V20a1 1 0 01-1 1A17 17 0 013 4a1 1 0 011-1h3.5a1 1 0 011 1c0 1.25.2 2.45.6 3.6a1 1 0 01-.25 1z"/></svg></span>
      <span>Call Us On :<br>123.456.7890</span>
    </div>
    <div class="contact-chip em">
      <span class="chip-icon"><svg width="15" height="11" viewBox="0 0 16 11"><rect x=".5" y=".5" width="15" height="10" fill="none" stroke="#fff"/><path d="M.5.5l7.5 6 7.5-6M.5 10.5l5.5-5M15.5 10.5l-5.5-5" fill="none" stroke="#fff"/></svg></span>
      <span>Email<br>info@rtmarlowbuild.com</span>
    </div>
    <p class="copyright">Copyright ©2018 R.T.Marlow Construction Ltd. All Rights Reserved.</p>
    <div class="social" aria-label="Social links"><span></span><span></span><span></span><span></span></div>
  </footer>

</div>
</body>
</html>
```